Web Design Project

We are looking for a unified design of Corporate Website, Stationary (Including Letterhead and Envelopes), Business Cards, Email Footers and Sales & Marketing Brochures.

Color palette should include:
Black (R: 24, G:24, B:24)
Red (R:206, G:0, B:39)
Dark Grey (R:51, G:51, B:51)
Light Grey/Silver (R:203, G:203, B:203)

As we do business in North America and the UK, designs should be reflective of standard sizing for both regions.

Check out our website to better understand who we are: www.KLVR.com and a copy of our Logo has been uploaded for reference.
Updates

Hello all, we had not anticipated the volume of unique, high quality designs we have received, thank you all for your submissions. A team review of all designs will take place the week of December 8th, and final decisions and selections made. Thank you again

Target Market(s)

Automotive Parts Wholesalers, Vehicle Repair Specialists, Automotive Parts Manufacturers, Automotive Insurance

Industry/Entity Type

Business

Font styles to use
Sans Serif

Requirements
Must have
• - Color palette should include:
- Black (R: 24, G:24, B:24)
- Red (R:206, G:0, B:39)
- Dark Grey (R:51, G:51, B:51)
- Light Grey/Silver (R:203, G:203, B:203)
Should not have
• No Animations

```html
<!DOCTYPE html>
<html lang="en">
<head>
<meta charset="utf-8">
<title>Kelvar Parts Solutions</title>
<link href="https://fonts.googleapis.com/css2?family=Libre+Franklin:wght@300;400;500;600&display=swap" rel="stylesheet">
<style>
:root{
  --black:#181818;
  --red:#ce0027;
  --btn-red:#e04646;
  --dark:#333333;
  --silver:#cbcbcb;
  --text:#666666;
  --band:#f7f7f7;
  --footer:#3a3a3a;
  --white:#ffffff;
}
*{margin:0;padding:0;box-sizing:border-box}
html,body{width:820px;height:1200px;overflow:hidden;background:var(--white)}
body{font-family:"Libre Franklin",Arial,sans-serif;color:var(--text);position:relative}
.abs{position:absolute}

.site-header{left:0;top:0;width:820px;height:70px}
.brand{left:90px;top:16px;display:flex;align-items:center;gap:8px}
.brand-dot{width:30px;height:30px;border-radius:50%;border:4px solid #8a8a8a}
.brand-name{font-size:17px;font-weight:600;color:var(--black);letter-spacing:.5px}
.utility{right:90px;top:32px;font-size:9px;color:#555;display:flex;gap:8px}
.utility .active{color:var(--red)}

.main-nav{left:0;top:70px;width:820px;height:33px;background:var(--dark);display:flex;align-items:center;padding-left:100px}
.main-nav a{color:#eee;font-size:9px;text-decoration:none;letter-spacing:.2px;margin-right:26px}

.hero{left:0;top:103px;width:820px;height:302px;background:radial-gradient(ellipse at 50% 50%,#ffffff 55%,#f0dde0 100%)}
.hero-visual{left:100px;top:30px;width:320px;height:245px;border-radius:12px;background:radial-gradient(circle at 50% 45%,#a8a9ad,#dcdcde 68%,#fbf6f6)}
.hero-title{left:466px;top:76px;font-size:23px;font-weight:600;color:var(--dark);line-height:33px;width:280px;white-space:nowrap}
.hero-text{left:467px;top:161px;width:262px;font-size:9px;font-weight:500;line-height:16.5px;color:#555}
.arrow{top:140px}

.features{left:0;top:470px;width:820px;display:flex;justify-content:center}
.feature{width:220px;text-align:center}
.feature-icon{margin:6px auto 12px;width:52px;height:52px;border-radius:8px;background:linear-gradient(#4a4a4a,#2e2e2e)}
.feature h3{font-size:12.5px;font-weight:400;color:var(--red);line-height:17px}
.feature p{font-size:8.5px;line-height:16.5px;margin-top:10px}

.opportunity{left:0;top:643px;width:820px;height:200px;background:var(--band);text-align:center}
.opportunity h2{font-size:16.5px;font-weight:500;color:var(--dark);margin-top:30px}
.opportunity p{font-size:8.5px;line-height:18.5px;width:618px;margin:15px auto 0}
.btn{display:inline-block;margin-top:17px;background:var(--btn-red);color:#fff;font-size:8.5px;padding:10px 17px;text-decoration:none;letter-spacing:.2px}

.card{top:885px;height:145px;border:1px solid #ddd;background:#fff}
.card-awards{left:90px;width:309px}
.card-quote{left:422px;width:308px}
.award-mark{left:13px;top:20px;display:flex;align-items:center;gap:5px}
.award-dot{width:14px;height:14px;border-radius:50%;background:var(--red)}
.award-name{font-size:12px;font-weight:600;color:var(--red)}
.card-title{left:148px;top:23px;font-size:12.5px;line-height:18px;color:var(--dark)}
.card-text{left:15px;top:72px;width:285px;font-size:8.5px;line-height:18.5px}
.card-text a{color:var(--red);text-decoration:none}
.quote-text{left:14px;top:14px;width:285px;font-size:8.5px;line-height:18.5px}
.avatar{left:74px;top:84px;width:44px;height:44px;border-radius:50%;border:2px solid #ddd;background:linear-gradient(#d9d2cc,#8b8884)}
.person{left:133px;top:94px}
.person strong{display:block;font-size:10.5px;font-weight:400;color:var(--red)}
.person span{font-size:8.5px}

.partners{left:95px;top:1087px;width:640px;display:flex;align-items:center;justify-content:space-between}
.partner{width:26px;height:22px;border-radius:50%;background:#d4d4d4}

.site-footer{left:0;top:1145px;width:820px;height:55px;background:var(--footer)}
.copyright{left:90px;top:22px;font-size:8.5px;color:#ddd}
.social{left:612px;top:18px;display:flex;gap:4px}
.social span{width:20px;height:20px;border-radius:50%;background:#fff}
</style>
</head>
<body>

<header class="abs site-header">
  <div class="abs brand"><span class="brand-dot"></span><span class="brand-name">Kelvar Parts Solutions</span></div>
  <div class="abs utility"><span>CDN</span><span>UK</span><span class="active">USA</span><span>&nbsp;|&nbsp;Supplier Login</span><span>&nbsp;|&nbsp;Kelvar Awards</span></div>
</header>

<nav class="abs main-nav">
  <a>HOME</a><a>INTELLIGENT SALES &amp; MARKETING</a><a>KELVAR AWARDS</a><a>REFERENCES</a><a>ABOUT US</a><a>CAREERS</a><a>CONTACT US</a>
</nav>

<section class="abs hero">
  <div class="abs hero-visual" role="img" aria-label="Assorted automotive parts: wheel, battery, exhaust, brake pads, suspension spring and steering wheel"></div>
  <h1 class="abs hero-title">Genuine Parts Sales<br>&amp; Marketing</h1>
  <p class="abs hero-text">We offer a unique multi-brand solution to both OE suppliers and the automotive repairers by combining professionally managed parts.</p>
  <svg class="abs arrow" style="left:44px" width="14" height="22" viewBox="0 0 14 22"><path d="M11 2 3 11l8 9" fill="none" stroke="#444" stroke-width="3.5"/></svg>
  <svg class="abs arrow" style="left:764px" width="14" height="22" viewBox="0 0 14 22"><path d="M3 2l8 9-8 9" fill="none" stroke="#bbb" stroke-width="3.5"/></svg>
</section>

<section class="abs features">
  <div class="feature">
    <div class="feature-icon" role="img" aria-label="Icon of a car raised on a workshop lift"></div>
    <h3>Automotive<br>Parts Wholesalers</h3>
    <p>Neque porro quisquam est qui dolorem ipm<br>quia dolor sit adipisci velit.</p>
  </div>
  <div class="feature">
    <div class="feature-icon" role="img" aria-label="Icon of a vehicle mechanic"></div>
    <h3>Vehicle<br>Repair Specialists</h3>
    <p>Neque porro quisquam est qui dolorem ipm<br>quia dolor sit adipisci velit.</p>
  </div>
  <div class="feature">
    <div class="feature-icon" role="img" aria-label="Icon of a shock absorber beside a tyre"></div>
    <h3>Automotive<br>Parts Manufacturers</h3>
    <p>Neque porro quisquam est qui dolorem ipm<br>quia dolor sit adipisci velit.</p>
  </div>
</section>

<section class="abs opportunity">
  <h2>The Opportunity</h2>
  <p>OE Wholesale Parts provide significant opportunities for both OE dealership suppliers and repairers to capture new and incremental profits. On behalf of our local ‘Best in Class’ parts wholesalers our team of qualified parts experts work with repairers to maximize these profits. We offer a unique multi-brand solution to both OE suppliers and the automotive repairers by combining professionally managed parts.</p>
  <a class="btn">WATCH OUR CORPORATE VIDEO</a>
</section>

<article class="abs card card-awards">
  <div class="abs award-mark"><span class="award-dot"></span><span class="award-name">Kelvar Awards</span></div>
  <div class="abs card-title">Kelvar<br>Parts Rewards</div>
  <p class="abs card-text">Our Kelvar Awards wholesale parts loyalty program is designed specifically for the automotive repair industry. Repairers earn Reward Points from multiple suppliers. &nbsp;<a>[ Read More ]</a></p>
</article>

<article class="abs card card-quote">
  <p class="abs quote-text">We have been very satisfied with the new contacts that Kelvar has brought us and the reinforcing of existing wholesale relationships through this time. Repairers earn Reward Points.</p>
  <svg class="abs" style="left:36px;top:100px" width="10" height="14" viewBox="0 0 10 14"><path d="M8 1 2 7l6 6" fill="none" stroke="#aaa" stroke-width="2.5"/></svg>
  <div class="abs avatar" role="img" aria-label="Portrait of the customer quoted"></div>
  <div class="abs person"><strong>Dan Merrow,</strong><span>Parts Manager Harbor Motors</span></div>
  <svg class="abs" style="left:270px;top:100px" width="10" height="14" viewBox="0 0 10 14"><path d="M2 1l6 6-6 6" fill="none" stroke="#ccc" stroke-width="2.5"/></svg>
</article>

<div class="abs partners">
  <svg width="10" height="14" viewBox="0 0 10 14"><path d="M8 1 2 7l6 6" fill="none" stroke="#aaa" stroke-width="2.5"/></svg>
  <span class="partner"></span><span class="partner"></span><span class="partner"></span><span class="partner"></span><span class="partner"></span><span class="partner"></span><span class="partner"></span><span class="partner"></span><span class="partner"></span><span class="partner"></span><span class="partner"></span><span class="partner"></span><span class="partner"></span><span class="partner"></span><span class="partner"></span><span class="partner"></span>
  <svg width="10" height="14" viewBox="0 0 10 14"><path d="M2 1l6 6-6 6" fill="none" stroke="#ccc" stroke-width="2.5"/></svg>
</div>

<footer class="abs site-footer">
  <p class="abs copyright">Copyright © 2014 Yoursite. All rights reserved.</p>
  <div class="abs social"><span></span><span></span><span></span><span></span><span></span></div>
</footer>

</body>
</html>
```